Letterhead and business card design

We have recently had a logo designed by brandnestly. now we need a corporate identity with business card and lettehead design.

Target Market(s)

law firms corporates

Industry/Entity Type

Business

Requirements
Should not have
• cheesy detecive stuff like magnifying glasses etxcc

```html
<!DOCTYPE html>
<html lang="en">
<head>
<meta charset="utf-8">
<title>Hargrove &amp; Lindqvist — Business Card</title>
<link rel="stylesheet" href="https://fonts.googleapis.com/css2?family=Questrial&family=Cormorant+Garamond:ital,wght@1,500&display=swap">
<style>
  :root {
    --backdrop: #3a3a3a;
    --card-front: #f6f6f5;
    --card-back-top: #8a8e8b;
    --card-back-bottom: #5e625f;
    --band-top: #a9aca9;
    --band-bottom: #7d817e;
    --ink-dark: #3d3f3e;
    --ink-mid: #555857;
    --ink-soft: #6e716f;
    --ink-light: #f1f2f0;
    --ink-light-soft: #dcdedb;
  }
  * { box-sizing: border-box; margin: 0; padding: 0; }
  html, body { width: 1200px; height: 1000px; overflow: hidden; }
  body {
    position: relative;
    background: var(--backdrop);
    font-family: "Questrial", "Century Gothic", sans-serif;
  }
  .card {
    position: absolute;
    width: 529px;
    height: 302px;
    border-radius: 14px;
    overflow: hidden;
    text-align: center;
  }
  .card-front { left: 181px; top: 169px; background: var(--card-front); }
  .card-back {
    left: 473px; top: 549px;
    background: linear-gradient(180deg, var(--card-back-top), var(--card-back-bottom));
  }
  .brand-name {
    position: absolute; left: 0; right: 0; top: 50px;
    font-size: 29px; letter-spacing: 1px;
    color: var(--ink-mid);
  }
  .card-back .brand-name { color: var(--ink-light); }
  .tagline {
    position: absolute; left: 0; right: 0; top: 92px;
    font-family: "Cormorant Garamond", Georgia, serif;
    font-style: italic; font-weight: 500;
    font-size: 16px; color: var(--ink-soft);
  }
  .card-back .tagline { color: var(--ink-light-soft); }
  .person-name {
    position: absolute; left: 0; right: 0; top: 166px;
    font-size: 15px; font-weight: 700; letter-spacing: 0.5px;
    color: var(--ink-dark);
  }
  .person-role {
    position: absolute; left: 0; right: 0; top: 186px;
    font-size: 12px; color: var(--ink-mid);
  }
  .address {
    position: absolute; left: 0; right: 0; top: 238px;
    font-size: 12px; color: var(--ink-mid);
  }
  .contact-line {
    position: absolute; left: 0; right: 0; top: 258px;
    font-size: 12px; color: var(--ink-mid);
  }
  .contact-line b { color: var(--ink-dark); }
  .footer-band {
    position: absolute; left: 0; right: 0; bottom: 0; height: 21px;
    background: linear-gradient(180deg, var(--band-top), var(--band-bottom));
  }
  .website {
    position: absolute; left: 0; right: 0; top: 258px;
    font-size: 12px; color: var(--ink-light-soft);
  }
</style>
</head>
<body>
  <section class="card card-front">
    <div class="brand-name">HARGROVE &amp; LINDQVIST</div>
    <div class="tagline">Investigations • Security • Intelligence</div>
    <div class="person-name">MARTIN LINDQVIST</div>
    <div class="person-role">Director</div>
    <div class="address">PO Box 918, Harbour Lane, Wellton, New Zealand</div>
    <div class="contact-line"><b>Tel:</b> +64 9 555 0142 &nbsp;•&nbsp; <b>Fax:</b> +64 9 555 0187 &nbsp;•&nbsp; <b>Email:</b> martin@thecasework.co.nz</div>
    <div class="footer-band"></div>
  </section>

  <section class="card card-back">
    <div class="brand-name">HARGROVE &amp; LINDQVIST</div>
    <div class="tagline">Investigations • Security • Intelligence</div>
    <div class="website">www.thecasework.co.nz</div>
  </section>
</body>
</html>
```